Creation of a Valterna Flyer design

As part of the cr% 26 # 233; ation of our soci% 26 # 233; t% 26 # 233 ;, we wish to cr% 26 # 233; er a flyer pr% 26 # 233; feeling our diff% 26 # 233; annuities% 26 # 233; s business advisory services% 26 # 233; foreign% 26 # 232; res who wish to develop their activities% 26 # 233; s in Switzerland. We want a double-sided flyer that presents% 26 # 233; society% 26 # 233; t% 26 # 233; d% 26 # 39; a c% 26 # 244; t% 26 # 233; and who presents% 26 # 233; benefits of the other. We have d% 26 # 233; j% 26 # 224; made a very basic provisional flyer to be able to present our activities. We put it to you as an example.

Target Market(s)

European companies% 26 # 233; internal% 26 # 233; res% 26 # 233; es by the market% 26 # 233; Swiss

Industry/Entity Type

Business Consultant

Colors

Designer to choose colors to be used in the design.

Requirements
Must have
• Company name and contact details
A field to detail the services
Nice to have
• Some% 26 # 233; l% 26 # 233; elements that recall Switzerland and some% 26 # 233; l% 26 # 233; elements that recall c% 26 # 244; t% 26 # 233; % 26quot; business% 26quot;

```html
<!DOCTYPE html>
<html lang="en">
<head>
<meta charset="utf-8">
<title>Valterna Flyer</title>
<link href="https://fonts.googleapis.com/css2?family=Inter:wght@400;700&display=swap" rel="stylesheet">
<style>
  :root {
    --navy: #223f53;
    --ink: #1f3a4f;
    --paper: #ffffff;
    --paper-tint: #e4edf4;
    --stage: #1c5b85;
    --sky-top: #6f9cc9;
    --sky-pale: #dbe7f2;
    --snow: #eef2f6;
    --meadow: #a8864f;
    --lake: #49b8c4;
    --forest: #5e7f4a;
  }
  * { box-sizing: border-box; margin: 0; padding: 0; }
  html, body { width: 1200px; height: 1200px; overflow: hidden; }
  body {
    background: var(--stage);
    font-family: "Inter", Arial, sans-serif;
    position: relative;
  }
  .flyer {
    position: absolute;
    left: 160px;
    top: 30px;
    width: 880px;
    height: 1140px;
    background: linear-gradient(180deg, var(--paper) 52%, var(--paper-tint) 100%);
    overflow: hidden;
    color: var(--ink);
  }
  .hero-photo {
    position: absolute;
    left: 0; top: 0;
    width: 880px; height: 440px;
    background: linear-gradient(180deg, var(--sky-top) 0%, var(--sky-pale) 30%, var(--snow) 52%, #9c8f86 66%, var(--meadow) 80%, #c9c3b4 100%);
  }
  .waves {
    position: absolute;
    left: 0; top: 0;
    width: 880px; height: 600px;
  }
  .brand {
    position: absolute;
    left: 403px;
    top: 63px;
    display: flex;
    align-items: center;
    gap: 34px;
  }
  .brand-square {
    width: 65px; height: 65px;
    border-radius: 12px;
    background: var(--navy);
  }
  .brand-name {
    font-size: 56px;
    font-weight: 400;
    letter-spacing: 3px;
    color: var(--navy);
    line-height: 1;
  }
  .intro {
    position: absolute;
    left: 60px;
    top: 426px;
    width: 760px;
    color: #ffffff;
    font-size: 19px;
    line-height: 24.5px;
    text-align: justify;
    text-align-last: center;
  }
  .headline {
    position: absolute;
    left: 40px;
    top: 588px;
    width: 800px;
    text-align: center;
    font-size: 26px;
    font-weight: 700;
    line-height: 33px;
    color: var(--ink);
  }
  .body-copy {
    position: absolute;
    left: 54px;
    top: 670px;
    width: 784px;
    font-size: 15.3px;
    line-height: 21px;
    color: var(--ink);
  }
  .body-copy p + p { margin-top: 20px; }
  .lake-photo {
    position: absolute;
    left: 0; top: 892px;
    width: 880px; height: 248px;
    background:
      linear-gradient(180deg, rgba(255,255,255,0) 0%, rgba(255,255,255,0) 60%, var(--lake) 78%, #2fa6b6 100%),
      linear-gradient(90deg, var(--forest) 0%, #b58a62 30%, #c9a27a 55%, #cfe0ec 65%, #dbe8f2 100%);
  }
  .footnote {
    position: absolute;
    right: 55px;
    top: 914px;
    font-size: 13px;
    color: var(--ink);
  }
  .brand-small {
    position: absolute;
    left: 628px;
    top: 1085px;
    display: flex;
    align-items: center;
    gap: 14px;
  }
  .brand-small .brand-square {
    width: 27px; height: 27px;
    border-radius: 6px;
  }
  .brand-small .brand-name {
    font-size: 23px;
    letter-spacing: 1.5px;
  }
</style>
</head>
<body>
  <main class="flyer">
    <div class="hero-photo" role="img" aria-label="Snow-capped Alpine peak reflected in a mountain lake with golden autumn meadows"></div>

    <svg class="waves" viewBox="0 0 880 600" aria-hidden="true">
      <path class="wave-sliver" d="M0,265 C180,330 380,374 880,376 L880,600 L0,600 Z" fill="var(--navy)"/>
      <path class="wave-white" d="M0,315 C300,385 600,392 880,377 L880,600 L0,600 Z" fill="#ffffff"/>
      <path class="wave-band" d="M0,345 C300,400 600,405 880,385 L880,578 Q440,500 0,578 Z" fill="var(--navy)"/>
    </svg>

    <div class="brand">
      <span class="brand-square"></span>
      <span class="brand-name">VALTERNA</span>
    </div>

    <p class="intro">The potential of the Swiss market offers many business opportunities to foreign companies, however there are some tariff and non-tariff barriers to cope with, such as its strong requirements in terms of quality and innovation, cultural and linguistic differences, specific rules applied to certain products or services.</p>

    <h1 class="headline">Valterna is there to support you in your administrative<br>and strategic procedures!</h1>

    <div class="body-copy">
      <p>Valterna strives to deepen the understanding of your business and acts as your local partner.<br>We assist you in defining together all the services that best meet your needs.</p>
      <p>Our consulting skills are focused on high added value sectors, such as food and beverages, fashion &amp; lifestyle, products and services for leading industries (pharmaceutical, chemical, precision mechanics) or sustainable solutions (renewable energies, recyclable materials).</p>
      <p>From our office in Neuchatel* and with our language knowledges, we are able to cover the whole of Switzerland. Having many years of experience in economic promotion and business management, we are familiar with the Swiss trade and foreign companies wishing to export to Switzerland.</p>
    </div>

    <div class="lake-photo" role="img" aria-label="Lakeside castle with towers on turquoise water, green hills and distant Alps"></div>

    <p class="footnote">*as of August 2020, we will open an office in Zurich well</p>

    <div class="brand-small">
      <span class="brand-square"></span>
      <span class="brand-name">VALTERNA</span>
    </div>
  </main>
</body>
</html>
```